BRISKEL Need a luxury modern business card designed.

Need a luxury modern business card designed. refer to the uploaded files for the company name and logo in the zip file under source files. i will making my descion on monday. so please send in before then so if we need to edit we will have the time. we have a trade show coming up and im on a deadline for printer.

Target Market(s)

high end clients

Contact Information for Business Card

Company nAme and logo. Tobias Fennick Co-Founder / Project Manager Office # 555-318-7094 Cell # 555-642-1586 BRISKEL.CA Tobias@briskel-example.ca

Font styles to use
Other font styles liked:
• Modern

Requirements
Must have
• Company name and logo, contact info, using the black, gold and white color scheme.

```html
<!DOCTYPE html>
<html lang="en">
<head>
<meta charset="UTF-8">
<title>BRISKEL Business Card</title>
<link href="https://fonts.googleapis.com/css2?family=Roboto:wght@300;400;700&display=swap" rel="stylesheet">
<style>
  :root {
    --stage: #d9d6d1;
    --card-black: #262626;
    --card-white: #ffffff;
    --gold: #a89563;
    --ink: #2b2b2b;
    --ink-soft: #555555;
    --emboss: #1b1b1b;
  }
  html, body {
    margin: 0;
    padding: 0;
    width: 1200px;
    height: 900px;
    overflow: hidden;
    background: var(--stage);
    font-family: "Roboto", Arial, sans-serif;
  }
  .canvas {
    position: relative;
    width: 1200px;
    height: 900px;
  }
  .card {
    position: absolute;
    width: 580px;
    height: 331px;
    box-shadow: 0 10px 28px rgba(0,0,0,0.25);
    box-sizing: border-box;
  }
  .card-back {
    left: 120px;
    top: 70px;
    background: var(--card-black);
    display: flex;
    align-items: center;
    justify-content: center;
  }
  .back-brand {
    display: flex;
    align-items: center;
    gap: 14px;
    font-weight: 300;
    font-size: 46px;
    letter-spacing: 10px;
    color: var(--emboss);
    text-shadow: 0 1px 0 rgba(255,255,255,0.08);
  }
  .back-brand .mark-square {
    width: 22px;
    height: 22px;
    background: var(--emboss);
  }
  .card-front {
    left: 500px;
    top: 470px;
    background: var(--card-white);
  }
  .front-brand {
    position: absolute;
    left: 36px;
    top: 92px;
    display: flex;
    align-items: center;
    gap: 12px;
    font-weight: 300;
    font-size: 34px;
    letter-spacing: 7px;
    color: var(--ink);
  }
  .front-brand .mark-square {
    width: 16px;
    height: 16px;
    background: var(--ink);
  }
  .person {
    position: absolute;
    right: 30px;
    top: 118px;
    text-align: right;
  }
  .person-name {
    font-weight: 700;
    font-size: 21px;
    color: var(--gold);
    letter-spacing: 0.5px;
    margin: 0;
  }
  .person-title {
    font-weight: 400;
    font-size: 14px;
    color: var(--ink-soft);
    margin: 4px 0 0;
  }
  .divider {
    position: absolute;
    left: 30px;
    right: 30px;
    top: 178px;
    height: 1px;
    background: var(--gold);
  }
  .contact-list {
    position: absolute;
    left: 34px;
    top: 196px;
    margin: 0;
    padding: 0;
    list-style: none;
  }
  .contact-list li {
    display: flex;
    align-items: center;
    gap: 9px;
    font-size: 15px;
    color: var(--ink-soft);
    line-height: 24px;
  }
  .contact-list svg {
    width: 13px;
    height: 13px;
    flex: none;
  }
</style>
</head>
<body>
<div class="canvas">
  <section class="card card-back">
    <div class="back-brand"><span class="mark-square"></span>BRISKEL</div>
  </section>

  <section class="card card-front">
    <div class="front-brand"><span class="mark-square"></span>BRISKEL</div>

    <div class="person">
      <p class="person-name">TOBIAS FENNICK</p>
      <p class="person-title">Co-Founder / Project Manager</p>
    </div>

    <div class="divider"></div>

    <ul class="contact-list">
      <li>
        <svg viewBox="0 0 16 16" aria-hidden="true"><path fill="#a89563" d="M3.5 1.5l2.5 0 1 3.5-1.6 1.2a8 8 0 0 0 4.4 4.4L11 9l3.5 1v2.5c0 .8-.7 1.5-1.5 1.5A12 12 0 0 1 2 3c0-.8.7-1.5 1.5-1.5z"/></svg>
        555-318-7094
      </li>
      <li>
        <svg viewBox="0 0 16 16" aria-hidden="true"><rect x="4" y="1" width="8" height="14" rx="1.5" fill="none" stroke="#a89563" stroke-width="1.5"/><circle cx="8" cy="12.5" r="0.9" fill="#a89563"/></svg>
        555-642-1586
      </li>
      <li>
        <svg viewBox="0 0 16 16" aria-hidden="true"><rect x="1" y="3.5" width="14" height="9" fill="#a89563"/><path d="M1 3.5l7 5 7-5" fill="none" stroke="#fff" stroke-width="1.2"/></svg>
        Tobias@briskel-example.ca
      </li>
      <li>
        <svg viewBox="0 0 16 16" aria-hidden="true"><circle cx="8" cy="8" r="6.5" fill="#a89563"/><path d="M1.5 8h13M8 1.5c-2.5 3-2.5 10 0 13M8 1.5c2.5 3 2.5 10 0 13" fill="none" stroke="#fff" stroke-width="0.9"/></svg>
        BRISKEL.CA
      </li>
    </ul>
  </section>
</div>
</body>
</html>
```